Wordpress theme website for professionals working together

My partner and I are offering business services, my wife in the energy business as mainly as member of the board of commissioners. I am working as interim manager/consultant in the accounting and finance area. Both activities are connected in one company VELMOT BV (dutch ltd). We need a CV based website. Beside this we do some financial and accounting services.

Target Market(s)

small medium business

Font styles to use
Sans Serif

Colors

Designer to choose colors to be used in the design.

Requirements
Must have
• Pictures of both members.
• CLEAN AND SIMPLE
• I LIKE BLACK & WHITE
Nice to have
• I like design like this theme: http://theme.pruxelo-example.com/resume/

```html
<!DOCTYPE html>
<html lang="en">
<head>
<meta charset="utf-8">
<title>VELMOT BV</title>
<link rel="stylesheet" href="https://fonts.googleapis.com/css2?family=Roboto+Slab:wght@300;400&family=Arimo:wght@400;700&display=swap">
<style>
  :root {
    --ink: #2b2b2b;
    --muted: #6f6f6f;
    --paper: #ffffff;
    --light: #f2f2f2;
    --dark: #111111;
    --bar-fill: #9c9c9c;
    --line: #bdbdbd;
    --hero-a: #c9ced6;
    --hero-b: #eef0f3;
  }
  * { margin: 0; padding: 0; box-sizing: border-box; }
  html, body { width: 1200px; height: 3180px; overflow: hidden; }
  body { position: relative; background: var(--paper); color: var(--ink); font-family: "Arimo", Arial, sans-serif; }
  h1, h2, h3 { font-weight: 400; }
  .slab { font-family: "Roboto Slab", Georgia, serif; }
  section, header, footer { position: absolute; left: 0; width: 1200px; }

  /* header */
  .site-header { top: 0; height: 108px; background: var(--paper); }
  .brand { position: absolute; left: 112px; top: 38px; font-size: 30px; font-weight: 400; }
  .main-nav { position: absolute; right: 112px; top: 48px; display: flex; gap: 40px; font-size: 13px; }

  /* hero */
  .hero { top: 108px; height: 552px; background: linear-gradient(90deg, var(--hero-a), var(--hero-b) 55%, #dfe2e6); overflow: hidden; }
  .hero-photo { position: absolute; left: 520px; top: 0; width: 680px; height: 552px; background: radial-gradient(ellipse at 55% 45%, #b59a88 0%, #8f7a70 30%, #4a4d55 65%, #d8dadd 100%); }
  .hero-title { position: absolute; left: 112px; top: 118px; font-size: 64px; font-weight: 300; color: #3a3a3a; }
  .hero-text { position: absolute; left: 112px; top: 220px; width: 400px; font-size: 13px; line-height: 34px; color: #3a3a3a; }
  .btn-outline { position: absolute; left: 112px; top: 350px; width: 140px; height: 46px; border: 1px solid #8a8a8a; border-radius: 23px; font-size: 15px; display: flex; align-items: center; justify-content: center; }

  /* tabs */
  .tabs { top: 660px; height: 130px; }
  .tab { position: absolute; top: 40px; width: 168px; height: 50px; border-radius: 25px; font-size: 19px; display: flex; align-items: center; justify-content: center; border: 1px solid #9a9a9a; background: var(--paper); }
  .tab.active { left: 426px; background: #333; color: #fff; border-color: #333; }
  .tab.active::after { content: ""; position: absolute; bottom: -9px; left: 76px; border: 8px solid transparent; border-top-color: #333; border-bottom: 0; }
  .tab.second { left: 606px; }

  /* profile */
  .profile { top: 790px; height: 467px; background: var(--light); }
  .avatar { position: absolute; left: 120px; top: 40px; width: 142px; height: 142px; border-radius: 50%; border: 4px solid #fff; box-shadow: 0 0 0 1px #ccc; background: radial-gradient(circle at 50% 40%, #c7aa98, #55575e 70%, #2a2c33); }
  .profile-name { position: absolute; left: 288px; top: 50px; font-size: 24px; }
  .timeline { position: absolute; left: 292px; top: 118px; width: 1px; height: 140px; background: var(--line); }
  .dot { position: absolute; left: 287px; width: 11px; height: 11px; border-radius: 50%; }
  .dot.filled { top: 113px; background: #555; }
  .dot.open { top: 253px; border: 1px solid #555; background: var(--light); }
  .job-group { position: absolute; left: 314px; font-size: 16px; }
  .job { position: absolute; left: 453px; }
  .job h4 { font-size: 13px; font-weight: 700; color: #111; }
  .job p { font-size: 11px; color: #555; margin-top: 12px; }

  /* skills */
  .skills { top: 1257px; height: 491px; background: var(--dark); color: #fff; }
  .skills-title { position: absolute; left: 155px; top: 32px; font-size: 28px; }
  .skill { position: absolute; left: 253px; width: 785px; }
  .skill-label { font-size: 11px; color: #ddd; }
  .skill-bar { position: relative; margin-top: 16px; height: 9px; background: #fff; border-radius: 5px; }
  .skill-fill { height: 9px; background: var(--bar-fill); border-radius: 5px 0 0 5px; }
  .skill-pct { position: absolute; top: -26px; transform: translateX(-50%); font-size: 9px; color: #ddd; border: 1px solid #aaa; padding: 2px 5px; background: var(--dark); }

  /* education */
  .education { top: 1748px; height: 197px; background: var(--light); text-align: center; }
  .section-title { font-size: 32px; font-weight: 400; }
  .education .section-title { position: absolute; width: 100%; top: 38px; }
  .edu-chip { position: absolute; top: 104px; width: 130px; height: 36px; border: 1px solid #999; background: #fff; font-size: 12px; display: flex; align-items: center; justify-content: center; }

  /* worked for */
  .worked { top: 1945px; height: 475px; background: var(--dark); color: #fff; }
  .worked-title { position: absolute; left: 122px; top: 60px; font-size: 26px; }
  .worked-intro { position: absolute; left: 287px; top: 52px; width: 760px; font-size: 11px; line-height: 27px; color: #ccc; }
  .employer { position: absolute; top: 158px; width: 380px; }
  .employer h3 { font-size: 20px; font-weight: 400; margin-bottom: 22px; }
  .employer ul { list-style: none; }
  .employer li { display: flex; align-items: center; gap: 18px; font-size: 11px; color: #ccc; height: 38.5px; }

  /* photography */
  .gallery { top: 2420px; height: 672px; background: var(--light); text-align: center; }
  .gallery .section-title { position: absolute; width: 100%; top: 44px; font-size: 30px; }
  .gallery-intro { position: absolute; width: 100%; top: 106px; font-size: 11px; color: #444; }
  .gallery-grid { position: absolute; left: 112px; top: 150px; width: 976px; height: 455px; display: grid; grid-template-columns: repeat(4, 1fr); grid-template-rows: repeat(2, 1fr); gap: 2px; }
  .gallery-item { background: linear-gradient(135deg, #c9ccd1, #5e6673); }
  .gallery-item.warm { background: linear-gradient(135deg, #d8d4cd, #6f6a66); }
  .gallery-item.deep { background: linear-gradient(135deg, #4c5a70, #1f2a3c); }

  /* footer */
  .site-footer { top: 3092px; height: 88px; background: var(--dark); color: #ddd; }
  .copyright { position: absolute; left: 112px; top: 38px; font-size: 11px; }
  .social { position: absolute; left: 878px; top: 26px; display: flex; gap: 6px; }
  .social span { width: 37px; height: 37px; border: 2px solid #ddd; border-radius: 50%; }
</style>
</head>
<body>

<header class="site-header">
  <div class="brand slab">VELMOT BV</div>
  <nav class="main-nav slab"><span>Home</span><span>About Us</span><span>Job</span><span>Skills</span><span>Education</span><span>Contact Us</span></nav>
</header>

<section class="hero">
  <div class="hero-photo" role="img" aria-label="Portrait photo of a smiling man with glasses"></div>
  <h1 class="hero-title slab">VELMOT BV</h1>
  <p class="hero-text slab">Sed ut perspiciatis unde omnis iste natus error sit voluptatem accusantium doloremque laudantium, totam rem aperiam, eaque ipsa quae ab illo inverto quasi architecto beatae vitae dicta sunt explicabo.</p>
  <div class="btn-outline slab">Read More</div>
</section>

<section class="tabs">
  <div class="tab active slab">Joris</div>
  <div class="tab second slab">Lotte</div>
</section>

<section class="profile">
  <div class="avatar" role="img" aria-label="Round portrait photo of Joris"></div>
  <h2 class="profile-name slab">Joris</h2>
  <div class="timeline"></div>
  <span class="dot filled"></span>
  <span class="dot open"></span>
  <div class="job-group slab" style="top:110px">Actual Jobs :</div>
  <div class="job-group slab" style="top:248px">Finished Jobs :</div>
  <div class="job" style="top:114px"><h4>Advisor Velder</h4><p>Sed ut perspiciatis unde omnis iste natus error sit voluptatem accusantium doloremque laudantium</p></div>
  <div class="job" style="top:174px"><h4>Advisor Brink &amp; Maker</h4><p>Sed ut perspiciatis unde omnis iste natus error sit voluptatem accusantium</p></div>
  <div class="job" style="top:252px"><h4>Controller a.i. Velder</h4><p>Sed ut perspiciatis unde omnis iste natus error sit voluptatem accusantium</p></div>
  <div class="job" style="top:312px"><h4>Advisor Solvara Green</h4><p>Sed ut perspiciatis unde omnis iste natus error sit voluptatem</p></div>
  <div class="job" style="top:372px"><h4>Financial director QRT</h4><p>Sed ut perspiciatis unde omnis iste natus</p></div>
</section>

<section class="skills">
  <h2 class="skills-title slab">Skills :</h2>
  <div class="skill" style="top:46px"><div class="skill-label">Annual Reporting</div><div class="skill-bar"><div class="skill-fill" style="width:62%"></div><span class="skill-pct" style="left:62%">65%</span></div></div>
  <div class="skill" style="top:107px"><div class="skill-label">Financial monthly reporting</div><div class="skill-bar"><div class="skill-fill" style="width:88%"></div><span class="skill-pct" style="left:88%">85%</span></div></div>
  <div class="skill" style="top:168px"><div class="skill-label">Accounting</div><div class="skill-bar"><div class="skill-fill" style="width:78%"></div><span class="skill-pct" style="left:78%">75%</span></div></div>
  <div class="skill" style="top:230px"><div class="skill-label">Financial management</div><div class="skill-bar"><div class="skill-fill" style="width:62%"></div><span class="skill-pct" style="left:62%">65%</span></div></div>
  <div class="skill" style="top:291px"><div class="skill-label">Project management</div><div class="skill-bar"><div class="skill-fill" style="width:52%"></div><span class="skill-pct" style="left:52%">50%</span></div></div>
  <div class="skill" style="top:352px"><div class="skill-label">Team player</div><div class="skill-bar"><div class="skill-fill" style="width:38%"></div><span class="skill-pct" style="left:38%">30%</span></div></div>
  <div class="skill" style="top:413px"><div class="skill-label">shooter</div><div class="skill-bar"><div class="skill-fill" style="width:78%"></div><span class="skill-pct" style="left:78%">85%</span></div></div>
</section>

<section class="education">
  <h2 class="section-title slab">Education</h2>
  <div class="edu-chip slab" style="left:462px">Kavelo (RA</div>
  <div class="edu-chip slab" style="left:608px">Atheneum B</div>
</section>

<section class="worked">
  <h2 class="worked-title slab">Worked for :</h2>
  <p class="worked-intro">Sed ut perspiciatis unde omnis iste natus error sit voluptatem accusantium doloremque laudantium, quae ab illo inventore veritatis et quasi ab illo inventore veritatis et quasi architecto beatae vitae dicta sunt architecto beatae vitae dicta sunt explicabo.</p>
  <div class="employer" style="left:287px">
    <h3 class="slab">Dromer Advocaten&amp;Notarissen</h3>
    <ul>
      <li><svg width="11" height="9" viewBox="0 0 11 9"><path d="M1 4.5l3 3L10 1" fill="none" stroke="#fff" stroke-width="2"/></svg>Sed ut perspiciatis unde omnis iste natus</li>
      <li><svg width="11" height="9" viewBox="0 0 11 9"><path d="M1 4.5l3 3L10 1" fill="none" stroke="#fff" stroke-width="2"/></svg>Error sit voluptatem accusantium</li>
      <li><svg width="11" height="9" viewBox="0 0 11 9"><path d="M1 4.5l3 3L10 1" fill="none" stroke="#fff" stroke-width="2"/></svg>Doloremque laudantium, totam</li>
      <li><svg width="11" height="9" viewBox="0 0 11 9"><path d="M1 4.5l3 3L10 1" fill="none" stroke="#fff" stroke-width="2"/></svg>Rem aperiam, eaque ipsa quae ab</li>
      <li><svg width="11" height="9" viewBox="0 0 11 9"><path d="M1 4.5l3 3L10 1" fill="none" stroke="#fff" stroke-width="2"/></svg>Beatae vitae dicta sunt explicabo</li>
    </ul>
  </div>
  <div class="employer" style="left:688px">
    <h3 class="slab">Halvorsen Audit</h3>
    <ul>
      <li><svg width="11" height="9" viewBox="0 0 11 9"><path d="M1 4.5l3 3L10 1" fill="none" stroke="#fff" stroke-width="2"/></svg>Sed ut perspiciatis unde omnis iste natus</li>
      <li><svg width="11" height="9" viewBox="0 0 11 9"><path d="M1 4.5l3 3L10 1" fill="none" stroke="#fff" stroke-width="2"/></svg>Error sit voluptatem accusantium</li>
      <li><svg width="11" height="9" viewBox="0 0 11 9"><path d="M1 4.5l3 3L10 1" fill="none" stroke="#fff" stroke-width="2"/></svg>Doloremque laudantium, totam</li>
      <li><svg width="11" height="9" viewBox="0 0 11 9"><path d="M1 4.5l3 3L10 1" fill="none" stroke="#fff" stroke-width="2"/></svg>Rem aperiam, eaque ipsa quae ab</li>
      <li><svg width="11" height="9" viewBox="0 0 11 9"><path d="M1 4.5l3 3L10 1" fill="none" stroke="#fff" stroke-width="2"/></svg>Beatae vitae dicta sunt explicabo</li>
    </ul>
  </div>
</section>

<section class="gallery">
  <h2 class="section-title slab">Fotography</h2>
  <p class="gallery-intro">Sed ut perspiciatis unde omnis iste natus error sit voluptatem accusantium doloremque laudantium, totam rem aperiam</p>
  <div class="gallery-grid">
    <div class="gallery-item" role="img" aria-label="Business colleagues working at a laptop"></div>
    <div class="gallery-item warm" role="img" aria-label="Colleagues meeting in a bright office"></div>
    <div class="gallery-item deep" role="img" aria-label="Hands over documents during a business meeting"></div>
    <div class="gallery-item deep" role="img" aria-label="Team discussing charts at a table"></div>
    <div class="gallery-item" role="img" aria-label="Two businessmen talking at a desk"></div>
    <div class="gallery-item warm" role="img" aria-label="Colleagues collaborating at a laptop"></div>
    <div class="gallery-item deep" role="img" aria-label="Professionals in conversation at the office"></div>
    <div class="gallery-item" role="img" aria-label="Businesswoman holding a notebook"></div>
  </div>
</section>

<footer class="site-footer">
  <p class="copyright">© Copyright-2018 VELMOT BV.All rights reserved.</p>
  <div class="social" aria-label="Social links"><span></span><span></span><span></span><span></span><span></span></div>
</footer>

</body>
</html>
```